Tusk Hollow Lodge website (design only)

Tusk Hollow Lodge (http://www.tuskhollowlodge-mw.example) is a private Safari lodge located in Malawi.
We would like a modern, professional website designed that does not subscribe to the cliched view of a Safari in Africa, but still maintain a wildlife/safari atmosphere.

The aim of our website is to entice people & drive them to the booking form.

Here are some examples of websites that we like. Although we would like our site to be a bit more in line with modern web design trends.

http://www.marulaplains.example/
http://www.kovunde.example/
http://www.tembalorecamp.example/

Requirements
Must have
• Here is a list of the pages required. Most of them will follow a standard content layout. I.e. heading, body and images.

If you take a look at the website, you will get an idea of hoe many page types there are +- 5

http://www.tuskhollowlodge-mw.example/index.htm

About Tusk Hollow
Lirundu Country Club
Rooms
Conferences
Cuisine
Facilities
Your Safari
Activities
Rates & Special Offers
Booking form
Latest Developments
How To Get There
Gallery
Contact Us
Blog / Newsfeed

```html
<!DOCTYPE html>
<html lang="en">
<head>
<meta charset="utf-8">
<title>Tusk Hollow Lodge</title>
<link rel="stylesheet" href="https://fonts.googleapis.com/css2?family=Arimo:wght@400;700&family=Cinzel:wght@700&display=swap">
<style>
:root{
  --charcoal:#262626;
  --charcoal-deep:#1b1b1b;
  --nav:#2c2c2c;
  --rust:#8a3a12;
  --heading:#6a2c0a;
  --sand:#dcb69c;
  --sand-shadow:#8b5a3a;
  --blush:#f7ebe3;
  --quote:#f3e6df;
  --muted:#bdbdbd;
  --white:#ffffff;
  --ink:#111111;
}
*{box-sizing:border-box;margin:0;padding:0}
html,body{width:698px;height:1200px;overflow:hidden}
body{position:relative;background:var(--blush);font-family:"Arimo",Arial,sans-serif;color:var(--ink)}
.abs{position:absolute}

/* header */
.site-header{left:0;top:0;width:698px;height:115px;background:var(--charcoal)}
.utility-links{right:16px;top:12px;font-size:9.5px;color:#cfcfcf;word-spacing:2px}
.utility-links span{margin:0 7px;color:#888}
.brand{left:14px;top:48px;display:flex;align-items:center;gap:8px}
.brand-dot{width:24px;height:24px;border-radius:50%;background:var(--rust)}
.brand-name{font-family:"Cinzel",Georgia,serif;font-weight:700;font-size:20px;line-height:24px;color:var(--white);letter-spacing:.3px}
.brand-place{left:73px;top:80px;font-family:"Cinzel",Georgia,serif;font-weight:700;font-size:11.5px;color:var(--white);letter-spacing:1px}
.search{left:431px;top:63px;width:201px;height:25px;background:var(--white);border-radius:3px;border:2px solid #ddd;font-size:9px;color:#999;padding:6px 10px}
.search-go{left:639px;top:62px;width:44px;height:26px;background:var(--rust);border:1px solid #d9a07a;border-radius:3px;color:var(--white);font-size:13px;text-align:center;line-height:24px}

/* nav */
.main-nav{left:0;top:115px;width:698px;height:33px;background:var(--nav);border-top:1px solid #3c3c3c;display:flex;font-size:9.5px;color:#ddd}
.main-nav a{color:inherit;text-decoration:none;line-height:32px;padding:0 5px;border-right:1px solid #1a1a1a;white-space:nowrap}
.main-nav a:first-child{padding-left:10px}
.main-nav a:last-child{border-right:0}

/* hero */
.hero{left:0;top:148px;width:698px;height:225px;background:linear-gradient(100deg,#6f6a4a 0%,#9a7a4a 25%,#b58c55 38%,#4f6a35 55%,#3d5a2b 80%,#2f4a24 100%)}
.hero-arrow{top:232px}

/* welcome card */
.card-back{left:14px;top:392px;width:458px;height:462px;background:var(--sand-shadow);transform:rotate(0.6deg)}
.welcome-card{left:12px;top:388px;width:458px;height:464px;background:var(--sand);border:4px solid var(--white);transform:rotate(-0.4deg);padding:22px 14px 0 14px}
.welcome-title{font-size:17.5px;font-weight:700;color:var(--heading);padding-bottom:8px;border-bottom:1px dashed var(--heading);margin-right:10px}
.welcome-card p{font-size:8.6px;line-height:16px;margin-top:14px;padding-right:8px}
.welcome-card p + p{margin-top:1px}
.welcome-photo{width:373px;height:159px;margin-top:14px;border:3px solid var(--white);background:linear-gradient(180deg,#c9d3dc 0%,#7d8c6a 35%,#8a5a44 55%,#4f8a35 75%,#3f7a2a 100%)}
.welcome-card .after-photo{margin-top:16px}
.btn{background:var(--rust);border:2px solid #c99a7c;color:var(--white);font-size:9.5px;text-align:center;border-radius:2px}
.read-more{left:360px;top:801px;width:82px;height:24px;line-height:20px}

/* booking */
.booking{left:500px;top:394px;width:174px;height:344px;background:var(--charcoal);border:2px solid var(--white);border-radius:3px;color:var(--white)}
.booking-title{font-size:14px;font-weight:700;padding:9px 11px 8px;border-bottom:1px dashed #aaa}
.field-label{left:11px;font-size:9px}
.field{left:11px;width:137px;height:20px;background:var(--white)}
.get-quote{left:77px;top:301px;width:84px;height:25px;line-height:21px}

.wildtrip{left:500px;top:752px;width:175px;height:109px;border:3px solid var(--white);border-radius:5px;background:linear-gradient(160deg,#a9542a,#7a3412);color:var(--white);padding:12px 12px}
.wildtrip-enjoy{font-size:16px;font-weight:700;letter-spacing:.5px}
.wildtrip-big{font-size:29px;font-weight:700;line-height:34px}
.wildtrip-big span{color:#d9a17a}
.wildtrip-link{position:absolute;right:16px;bottom:17px;font-size:9px;text-decoration:underline}

/* lower columns */
.col-title{top:873px;font-size:13px;font-weight:700;color:var(--heading)}
.divider{top:880px;width:0;height:142px;border-left:2px dotted var(--rust)}
.video{left:16px;top:898px;width:172px;height:115px;background:#1f1f1f}
.video-bar{left:0;bottom:0;width:172px;height:12px;background:#3a3a3a}
.gallery-photo{left:224px;top:899px;width:169px;height:116px;border:3px solid var(--white);background:linear-gradient(135deg,#6a7a5a,#a8784a 45%,#5a3a22)}
.quote-box{left:438px;top:899px;width:178px;height:101px;background:var(--quote);border:2px solid var(--white);padding:8px 10px;font-size:8px;line-height:17.5px}
.quote-name{color:#b86a2a;font-weight:700}
.silhouette{left:620px;top:966px;width:78px;height:71px;background:linear-gradient(180deg,#8a8a8a,#3a3a3a);border-radius:39px 39px 0 0}

/* footer */
.site-footer{left:0;top:1037px;width:698px;height:163px;background:var(--charcoal)}
.foot-col{top:1057px;font-size:9px;color:var(--muted);line-height:18.2px}
.copyright{left:0;top:1175px;width:698px;height:25px;background:linear-gradient(90deg,var(--charcoal-deep) 0%,var(--charcoal-deep) 40%,var(--charcoal) 70%);font-size:9px;color:var(--muted);padding:7px 0 0 10px}
.social{left:510px;width:137px;height:35px;border-bottom:1px dashed #999;display:flex;align-items:center;gap:17px;font-size:9px;color:var(--muted);white-space:nowrap}
.social i{width:22px;height:22px;border-radius:50%;background:#5a5a5a;display:block;flex:none}
</style>
</head>
<body>

<header class="site-header abs"></header>
<div class="utility-links abs">Home<span>|</span>Booking Requests<span>|</span>Sitemap</div>
<div class="brand abs"><i class="brand-dot"></i><span class="brand-name">Tusk Hollow Lodge</span></div>
<div class="brand-place abs">Nsanga Estate, Mkando</div>
<div class="search abs">Search what you want?</div>
<div class="search-go abs">GO</div>

<nav class="main-nav abs">
  <a>About Tusk Hollow</a><a>Rooms</a><a>Conferences</a><a>Cuisine</a><a>Facilities</a><a>Your Safari</a><a>Rates &amp; Special Offers</a><a>How to Get There</a><a>Gallery</a><a>Contact Us</a><a>Our Blog</a>
</nav>

<div class="hero abs" role="img" aria-label="Leopard resting on a rock among green bush"></div>
<svg class="hero-arrow abs" style="left:4px" width="20" height="30"><path d="M16 2 L4 15 L16 28" fill="none" stroke="#bbb" stroke-width="5"/></svg>
<svg class="hero-arrow abs" style="left:672px" width="20" height="30"><path d="M4 2 L16 15 L4 28" fill="none" stroke="#bbb" stroke-width="5"/></svg>

<div class="card-back abs"></div>
<section class="welcome-card abs">
  <h1 class="welcome-title">Welcome to Tusk Hollow Lodge</h1>
  <p>Warmest welcome to the unique Malawi experience. lodge complex, game park, the 18 hole Lirundu golf club and Kalembo dam.</p>
  <p>A multi million dollar development at Nsanga estate, Mkando on Kasiya road 20 kms from Lumbazi, the region's commercial capital creating a fascinating paradise for multiple leisure activities and conserving Malawi wildlife.Our Lodge also has beautifully designed and built in golden colored rock.</p>
  <div class="welcome-photo" role="img" aria-label="Brick lodge cottages with green roofs on a lawn"></div>
  <p class="after-photo">The 1st phase was completed in 2007, and is approx 1800 sq. meters, comprising of:<br>A fully carpeted and elegantly furnished restaurant with seating for up to 80 guests and exceptional cuisine to completely satisfy most palates. A stately carpeted conference hall for up to 45 people, 5 luxurious and spacious ensuite cottages with lounge and private verandah accessing a beautiful 18 meter swimming pool with cascading waterfall.</p>
</section>
<div class="read-more btn abs">Read More</div>

<aside class="booking abs">
  <h2 class="booking-title">Booking Enquiry</h2>
  <div class="field-label abs" style="top:43px">Name:</div>
  <div class="field abs" style="top:59px"></div>
  <div class="field-label abs" style="top:92px">E-Mail:</div>
  <div class="field abs" style="top:108px"></div>
  <div class="field-label abs" style="top:140px">Contact No.</div>
  <div class="field abs" style="top:155px"></div>
  <div class="field-label abs" style="top:188px">Message:</div>
  <div class="field abs" style="top:203px;width:149px;height:80px"></div>
  <div class="get-quote btn abs">Get Quote</div>
</aside>

<div class="wildtrip abs">
  <div class="wildtrip-enjoy">ENJOY</div>
  <div class="wildtrip-big">WILD<span>TRIP</span></div>
  <span class="wildtrip-link">Book Safari Now..</span>
</div>

<h3 class="col-title abs" style="left:18px">VIDEOS</h3>
<div class="divider abs" style="left:205px"></div>
<h3 class="col-title abs" style="left:224px">GALLERY</h3>
<div class="divider abs" style="left:417px"></div>
<h3 class="col-title abs" style="left:438px">TESTIMONIALS</h3>

<div class="video abs">
  <svg class="abs" style="left:71px;top:36px" width="30" height="30"><circle cx="15" cy="15" r="13" fill="none" stroke="#fff" stroke-width="2"/><path d="M11 8 L22 15 L11 22Z" fill="#fff"/></svg>
  <div class="video-bar abs"><div class="abs" style="left:48px;top:5px;width:80px;height:3px;background:#c0392b"></div></div>
</div>
<div class="gallery-photo abs" role="img" aria-label="Lodge lounge with cane chairs on a verandah"></div>
<div class="quote-box abs">
  "Esther and I have always appreciated their excellence in the customer service they provide the residency."<br>
  <span class="quote-name">Clara Mhone</span><br>(Residency Coordinator)
</div>
<svg class="abs" style="left:568px;top:998px" width="24" height="14"><path d="M0 0 L12 12 L24 0" fill="var(--quote)" stroke="#fff" stroke-width="2"/></svg>
<div class="silhouette abs" role="img" aria-label="Silhouette of the reviewer"></div>

<footer class="site-footer abs"></footer>
<div class="foot-col abs" style="left:41px">About Tusk Hollow<br>Rooms<br>Conferences<br>Cuisine<br>Facilities</div>
<div class="foot-col abs" style="left:160px">Rates &amp; Special Offers<br>How to Get There<br>Gallery<br>Contact Us<br>Our Blog</div>
<div class="foot-col abs" style="left:289px">Your Safari<br>Recent Developments<br>Activites<br>Booking Requests<br>Sitemap</div>
<div class="copyright abs">2012 © www.tuskhollowlodge-mw.example | All rights reserved</div>
<div class="social abs" style="top:1051px"><i></i>Follow Us on Friendlane</div>
<div class="social abs" style="top:1087px"><i></i>Tweet Us on Chirpline</div>
<div class="social abs" style="top:1121px"><i></i>Watch Us on ReelStream</div>
<div class="social abs" style="top:1155px"><i></i>Share us on Blog</div>

</body>
</html>
```